Bright Harbor Counseling Letterhead for hip modern business

I would like some ombre use of the colors in the logo hip letterhead that incorporates logo colors and feel, needs to connect with young professionals and college students. i need to be able to write letters to schools to excuse absences as well. i like color blocks on one side preferably using colors from the attached logo design.

Target Market(s)

high income young people, young adults and college students

Industry/Entity Type

mental health

Font styles to use
Serif
Sans Serif

Colors
0054AA
0677BA
7BADD7
CADEEF
E8F1F8
0094D4
00A9DD
6FCCEA
C7EBF8
E9F6FB
00AB8E
00BBA5
67D7C9
C6EFE9
E9F9F6
59FF00
82FF00
B8FF75
E3FFCB
F4FFEA
A7469A
B969AE
D3A5CF
EDDBEB
F8F0F9
6B429C
8869AF
B7A5CE
E3DAEB
F3F0F8

Requirements
Must have
• a modern hip feel, somewhat color

```html
<!DOCTYPE html>
<html lang="en">
<head>
<meta charset="utf-8">
<title>Bright Harbor Counseling Letterhead</title>
<link rel="stylesheet" href="https://fonts.googleapis.com/css2?family=Open+Sans:wght@300;400&display=swap">
<style>
  :root {
    --paper: #ffffff;
    --ink: #1a1a1a;
    --rule: #222222;
    --purple: #6B429C;
    --teal: #00AB8E;
    --blue: #0677BA;
    --wash-blue: #C7EBF8;
    --wash-pink: #EDDBEB;
    --wash-mint: #E9F9F6;
    --sig-tone: #ececec;
  }
  html, body {
    margin: 0;
    padding: 0;
    width: 882px;
    height: 1200px;
    overflow: hidden;
    background: var(--paper);
  }
  .letterhead {
    position: relative;
    width: 882px;
    height: 1200px;
    background: var(--paper);
    font-family: "Open Sans", Arial, sans-serif;
    color: var(--ink);
  }
  .brand {
    position: absolute;
    top: 62px;
    right: 82px;
    display: flex;
    align-items: flex-start;
    gap: 10px;
  }
  .brand-name {
    text-align: right;
    font-weight: 300;
    color: var(--ink);
    line-height: 1;
  }
  .brand-name .line-main {
    display: block;
    font-size: 36px;
    letter-spacing: 0.5px;
  }
  .brand-name .line-sub {
    display: block;
    font-size: 36px;
    margin-top: 4px;
    letter-spacing: 0.5px;
  }
  .brand-dot {
    width: 14px;
    height: 14px;
    border-radius: 50%;
    background: var(--purple);
    margin-top: 4px;
  }
  .letter-body {
    position: absolute;
    top: 196px;
    left: 89px;
    width: 701px;
    font-size: 15px;
    line-height: 22.9px;
    text-align: justify;
    hyphens: auto;
  }
  .letter-body p {
    margin: 0;
  }
  .signature {
    position: absolute;
    left: 505px;
    top: 726px;
    width: 280px;
    height: 125px;
    background: linear-gradient(135deg, #f4f4f4, var(--sig-tone));
    border-radius: 6px;
  }
  .corner-wash {
    position: absolute;
    left: 39px;
    top: 858px;
    width: 366px;
    height: 322px;
    background:
      radial-gradient(ellipse at 70% 45%, var(--wash-pink) 0%, rgba(237,219,235,0) 60%),
      radial-gradient(ellipse at 35% 30%, var(--wash-blue) 0%, rgba(199,235,248,0) 60%),
      radial-gradient(ellipse at 30% 80%, var(--wash-mint) 0%, rgba(233,249,246,0) 65%);
    opacity: 0.8;
  }
  .footer {
    position: absolute;
    left: 172px;
    right: 0;
    top: 1142px;
    border-top: 1.5px solid var(--rule);
    padding-top: 8px;
    display: flex;
    gap: 12px;
    padding-left: 11px;
    font-size: 13.5px;
    white-space: nowrap;
  }
  .contact-item {
    display: flex;
    align-items: center;
    gap: 5px;
  }
  .contact-icon {
    width: 17px;
    height: 17px;
    flex: none;
  }
</style>
</head>
<body>
<main class="letterhead">
  <header class="brand">
    <div class="brand-name">
      <span class="line-main">Bright Harbor</span>
      <span class="line-sub">Counseling</span>
    </div>
    <div class="brand-dot"></div>
  </header>

  <section class="letter-body">
    <p>Lorem ipsum dolor sit amet, consectetuer adipiscing elit, sed diam nonummy nibh euismod tincidunt ut laoreet dolore magna aliquam erat volutpat. Ut wisi enim ad minim veniam, quis nostrud exerci tation ullamcorper suscipit lobortis nisl ut aliquip ex ea commodo consequat. Duis autem vel eum iriure dolor in hendrerit in vulputate velit esse molestie consequat, vel illum dolore eu feugiat nulla facilisis at vero eros et accumsan et iusto odio dignissim qui blandit praesent luptatum zzril delenit augue duis dolore te feugait nulla facilisi.</p>
    <p>Lorem ipsum dolor sit amet, cons ectetuer adipiscing elit, sed diam nonummy nibh euismod tincidunt ut laoreet dolore magna aliquam erat volutpat. Ut wisi enim ad minim veniam, quis nostrud exerci tation ullamcorper suscipit lobortis nisl ut aliquip ex ea commodo consequat.</p>
    <p>Lorem ipsum dolor sit amet, consectetuer adipiscing elit, sed diam nonummy nibh euismod tincidunt ut laoreet dolore magna aliquam erat volutpat. Ut wisi enim ad minim veniam, quis nostrud exerci tation ullamcorper suscipit lobortis nisl ut aliquip ex ea commodo consequat. Duis autem vel eum iriure dolor in hendrerit in vulputate velit esse molestie consequat, vel illum dolore eu feugiat nulla facilisis at vero eros et accumsan et iusto odio dignissim qui blandit praesent luptatum zzril delenit augue duis dolore te feugait nulla facilisi.</p>
    <p>Lorem ipsum dolor sit amet, cons ectetuer adipiscing elit, sed diam nonummy nibh euismod tincidunt ut laoreet dolore magna aliquam erat volutpat. Ut wisi enim ad minim veniam, quis nostrud exerci tation ullamcorper suscipit lobortis nisl ut aliquip ex ea commodo consequat.</p>
    <p>Lorem ipsum dolor sit amet, consectetuer adipiscing elit, sed diam nonummy nibh euismod tincidunt ut laoreet dolore magna aliquam erat volutpat. Ut wisi enim ad minim veniam, quis nostrud exerci tation ullamcorper suscipit.</p>
  </section>

  <div class="signature" role="img" aria-label="Handwritten signature of the counselor"></div>

  <div class="corner-wash" role="img" aria-label="Soft pastel colour wash decoration"></div>

  <footer class="footer">
    <span class="contact-item">
      <svg class="contact-icon" viewBox="0 0 17 17" aria-hidden="true">
        <rect width="17" height="17" rx="4" fill="var(--purple)"/>
        <path d="M8.5 3.2a3.6 3.6 0 0 0-3.6 3.6c0 2.7 3.6 6.8 3.6 6.8s3.6-4.1 3.6-6.8a3.6 3.6 0 0 0-3.6-3.6z" fill="#fff"/>
        <circle cx="8.5" cy="6.8" r="1.4" fill="var(--purple)"/>
      </svg>
      240 Lantern Way, Maple Bend, Northland
    </span>
    <span class="contact-item">
      <svg class="contact-icon" viewBox="0 0 17 17" aria-hidden="true">
        <rect width="17" height="17" rx="4" fill="var(--teal)"/>
        <path d="M5.3 3.6l1.8-.3 1 2.6-1.2 1a6.5 6.5 0 0 0 3 3l1-1.2 2.6 1-.3 1.8c-.2.6-.8.9-1.4.8A8.8 8.8 0 0 1 4.5 5c0-.6.2-1.2.8-1.4z" fill="#fff"/>
      </svg>
      0917-382-615
    </span>
    <span class="contact-item">
      <svg class="contact-icon" viewBox="0 0 17 17" aria-hidden="true">
        <rect width="17" height="17" rx="4" fill="var(--blue)"/>
        <circle cx="8.5" cy="8.5" r="5" fill="none" stroke="#fff" stroke-width="1.2"/>
        <ellipse cx="8.5" cy="8.5" rx="2.2" ry="5" fill="none" stroke="#fff" stroke-width="1"/>
        <line x1="3.5" y1="8.5" x2="13.5" y2="8.5" stroke="#fff" stroke-width="1"/>
      </svg>
      www.brightharborcounsel.com
    </span>
  </footer>
</main>
</body>
</html>
```